Business is called "Keel Ledger". Accounting and tax services.

I need a flyer for my new business "Keel Ledger". I am an individual accountant working for himself on the Sunshine Coast in Queensland Australia. I would like to see designs that communicate reliability and trust. I believe my point of difference is that I am always available to my clients and I will cap my number of clients to ensure I can service them properly. Accountants in general seem to have a bad reputation for not responding to clients in a timely fashion, whether by email or phone. This is where I intend to differentiate myself. I have included my business card for ideas on colour and for contact information. I have also included some logo's that should go on the flyer. With the RFN logo, the words "Keel Ledger is a RFN Business" needs to be written either above, below or to the right hand side (as per the business card).

Target Market(s)

Small business owners and individuals requiring taxation and financials

Industry/Entity Type

Public Accounting

Font styles to use
Serif

Requirements
Must have
• Supplied logo's, accounting style pictures etc
Services: Small Business Taxation
Company & Trust Tax Returns
Rental Property Returns
Capital Gains Tax
Individual Tax Returns
BAS and IAS lodgements
Nice to have
• Needs to convey a sense of being reliable and responds to clients quickly.
Should not have
• My name

```html
<!DOCTYPE html>
<html lang="en">
<head>
<meta charset="utf-8">
<title>Keel Ledger – Flyer</title>
<link rel="stylesheet" href="https://fonts.googleapis.com/css2?family=Oswald:wght@500;600&family=Lato:wght@400;700&display=swap">
<style>
  :root{
    --stage:#137a64;
    --teal-deep:#1fa384;
    --teal-mid:#4fb9a0;
    --teal-pale:#8fd2c4;
    --ink:#141414;
    --paper:#ffffff;
    --badge-blue:#0b4f9c;
    --badge-gold:#fcd000;
    --ledgrio-blue:#1ab0e6;
  }
  *{margin:0;padding:0;box-sizing:border-box}
  html,body{width:1200px;height:1083px;overflow:hidden;background:var(--stage)}
  .flyer{
    position:absolute;left:247px;top:41px;width:1130px;height:1600px;
    transform:scale(0.625);transform-origin:0 0;
    background:var(--paper);overflow:hidden;
    box-shadow:0 30px 60px rgba(0,0,0,.35);
  }
  .shapes{position:absolute;inset:0}
  .brand{position:absolute;left:600px;top:10px;width:304px;text-align:center}
  .brand-mark{width:74px;height:74px;border:4px solid var(--ink);border-radius:50%;margin:0 auto 16px}
  .brand-name{font:400 27px/1 "Lato",sans-serif;letter-spacing:12px;color:var(--ink);padding-left:12px}
  .headline{position:absolute;left:78px;top:236px;color:var(--paper);font:600 112px/1 "Oswald",sans-serif;letter-spacing:-1px}
  .tagline{position:absolute;left:80px;top:368px;color:var(--ink);font:500 64px/1 "Oswald",sans-serif;letter-spacing:-0.5px}
  .intro{position:absolute;left:82px;top:543px;width:460px;color:var(--ink);font:400 30px/37px "Lato",sans-serif}
  .intro strong{font-weight:700}
  .phone{position:absolute;left:86px;top:737px;display:flex;align-items:center;gap:26px;color:var(--paper);font:500 68px/1 "Oswald",sans-serif}
  .services-title{position:absolute;left:78px;top:978px;color:var(--teal-deep);font:600 82px/1 "Oswald",sans-serif}
  .service-list{position:absolute;list-style:none;font:400 29px/27px "Lato",sans-serif;color:var(--ink)}
  .service-list li{position:relative;padding-left:40px}
  .service-list li::before{content:"";position:absolute;left:0;top:6px;width:17px;height:17px;background:var(--teal-mid)}
  .services-left{left:42px;top:1108px}
  .services-left li:nth-child(1){margin-bottom:28px}
  .services-left li:nth-child(2){margin-bottom:27px}
  .services-right{left:607px;top:1108px}
  .services-right li{margin-bottom:38px}
  .contact{position:absolute;left:38px;top:1462px;color:var(--ink);font:500 44px/50px "Oswald",sans-serif}
  .contact div{display:flex;align-items:center;gap:16px}
  .partners{position:absolute;left:625px;top:1385px;display:flex;align-items:center;gap:52px}
  .partner{display:flex;align-items:center;gap:12px;font:700 34px/1 "Lato",sans-serif;color:var(--ink)}
  .partner-dot{width:56px;height:56px;border-radius:50%;background:var(--ledgrio-blue)}
  .partner-square{width:56px;height:56px;background:var(--badge-blue)}
</style>
</head>
<body>
<main class="flyer">
  <svg class="shapes" viewBox="0 0 1130 1600" width="1130" height="1600" aria-hidden="false">
    <defs>
      <linearGradient id="photoTone" x1="0" y1="0" x2="1" y2="1">
        <stop offset="0" stop-color="#3b3e42"/>
        <stop offset="0.35" stop-color="#8f9092"/>
        <stop offset="0.55" stop-color="#c98a5a"/>
        <stop offset="0.75" stop-color="#ecebe8"/>
        <stop offset="1" stop-color="#f6f5f2"/>
      </linearGradient>
    </defs>
    <!-- upper hexagon: pale rim, mid body, deep top -->
    <polygon fill="var(--teal-pale)" points="0,194 350,0 765,227 1130,12 1130,880 553,1092 0,852"/>
    <polygon fill="var(--teal-mid)" points="15,208 350,18 765,250 1080,190 1080,905 553,1068 15,838"/>
    <polygon fill="var(--teal-deep)" points="15,208 350,18 765,250 1080,190 1080,490 15,507"/>
    <!-- photo hexagon -->
    <polygon role="img" aria-label="Photo of a calculator with a stack of copper coins" fill="url(#photoTone)" stroke="#000" stroke-width="22" stroke-linejoin="miter"
      points="950,170 1140,280 1140,980 957,1086 566,860 566,402"/>
    <!-- lower hexagon corner -->
    <polygon fill="var(--teal-pale)" points="0,1427 217,1297 615,1527 615,1600 0,1600"/>
    <polygon fill="var(--teal-deep)" points="0,1452 217,1325 595,1545 595,1600 0,1600"/>
  </svg>

  <header class="brand">
    <div class="brand-mark"></div>
    <div class="brand-name">KEEL LEDGER</div>
  </header>

  <h1 class="headline">Keel Ledger</h1>
  <p class="tagline">is a RFN Business"</p>

  <p class="intro">I am an individual accountant working for himself on the Sunshine <strong>Coast in Queensland Australia</strong></p>

  <div class="phone">
    <svg width="62" height="80" viewBox="0 0 62 80" aria-hidden="true">
      <path d="M12 4 L22 2 L28 22 L20 28 Q22 44 34 58 L42 52 L56 66 L48 76 Q30 80 16 58 Q2 34 12 4Z" fill="#000"/>
      <path d="M36 20 Q46 24 48 34 M38 12 Q54 18 56 34" stroke="#000" stroke-width="3" fill="none"/>
    </svg>
    <span>0412 555 018</span>
  </div>

  <h2 class="services-title">Services</h2>
  <ul class="service-list services-left">
    <li>Small Business Taxation</li>
    <li>Company &amp; Trust Tax<br>Returns</li>
    <li>Rental Property Returns</li>
  </ul>
  <ul class="service-list services-right">
    <li>Capital Gains Tax</li>
    <li>Individual Tax Returns</li>
    <li>BAS and IAS lodgements</li>
  </ul>

  <address class="contact" style="font-style:normal">
    <div>
      <svg width="30" height="22" viewBox="0 0 30 22" aria-hidden="true"><rect x="1" y="1" width="28" height="20" fill="none" stroke="#000" stroke-width="2"/><path d="M1 1 L15 12 L29 1 M1 21 L11 10 M29 21 L19 10" fill="none" stroke="#000" stroke-width="2"/></svg>
      <span>hello@keelledger.com.au</span>
    </div>
    <div>
      <svg width="30" height="30" viewBox="0 0 30 30" aria-hidden="true"><g fill="none" stroke="#000" stroke-width="2"><circle cx="15" cy="15" r="13"/><ellipse cx="15" cy="15" rx="6" ry="13"/><path d="M2 15 H28 M4 8 H26 M4 22 H26"/></g></svg>
      <span>www.keelledger.com.au</span>
    </div>
  </address>

  <div class="partners">
    <div class="partner"><span class="partner-dot"></span><span>Ledgrio</span></div>
    <div class="partner"><span class="partner-square"></span><span>RFN</span></div>
  </div>
</main>
</body>
</html>
```